Design a Travel and Tourism website

We would like a freelancer to design a website that is essentially easy to use and navigate database providing local information for Travelers about destination countries.

We proposed website would discuss different rates, fees, visa requirement, resort locations, cheap flights, etc. This website should be elegant and modern. Our business name is rovanix.
Some reference websites are zemplorift.ca, brindlefoxhaven.com,
There should be a forum in the website where travell\ers discuss about their first hand tranvel experience to such destinations.

Tourism

```html
<!DOCTYPE html>
<html lang="en">
<head>
<meta charset="utf-8">
<title>rovanix — Travel &amp; Tourism</title>
<link href="https://fonts.googleapis.com/css2?family=Montserrat:wght@400;600;700&family=Open+Sans:wght@400;600;700&display=swap" rel="stylesheet">
<style>
:root{
  --blue:#1b83c9;
  --blue-dark:#1466a3;
  --navy:#202a5e;
  --navy-deep:#161f4a;
  --gold:#b99a55;
  --gold-light:#c9ad6b;
  --ink:#333;
  --muted:#888;
  --line:#e3e3e3;
  --paper:#fff;
  --mist:#f1f1f1;
}
*{box-sizing:border-box;margin:0;padding:0}
html,body{width:1200px;height:3255px;overflow:hidden}
body{font-family:"Open Sans",Arial,sans-serif;color:var(--ink);background:var(--paper);position:relative}
.wrap{position:absolute;left:141px;width:918px}
h2.section-title{font-family:"Montserrat",Arial,sans-serif;font-weight:700;font-size:27px;text-align:center;letter-spacing:.5px}
.tabs-inline{text-align:center;font-size:12px;font-weight:600;margin-top:14px}
.tabs-inline span{padding:0 9px}
.tabs-inline .sep{padding:0;color:#bbb}

/* top navigation */
.topbar{position:absolute;top:0;left:0;width:1200px;height:63px;background:var(--blue)}
.utility{position:absolute;right:140px;top:4px;display:flex;gap:22px;font-size:9px;color:#cfe6f7;font-weight:600}
.nav{position:absolute;top:22px;display:flex;font-family:"Montserrat",Arial,sans-serif;font-size:12px;font-weight:700;color:#fff}
.nav a{display:block;padding:0 17px;line-height:41px;height:41px;color:#fff;text-decoration:none}
.nav a.active{background:var(--gold)}
.nav.left{left:141px}
.nav.right{left:715px}
.nav.right a{padding:0 23px}
.logo-shield{position:absolute;left:516px;top:0;width:168px;height:104px}
.logo-text{position:absolute;left:516px;top:22px;width:168px;text-align:center;font-family:"Montserrat",Arial,sans-serif;font-weight:700;font-size:26px;color:var(--navy)}

/* hero */
.hero{position:absolute;top:63px;left:0;width:1200px;height:349px;background:linear-gradient(135deg,#1d6f78 0%,#2a8a8c 35%,#3d7f5a 55%,#1d5f78 80%,#164f6a 100%)}
.hero h1{position:absolute;left:141px;top:200px;font-family:"Montserrat",Arial,sans-serif;font-weight:700;font-size:43px;line-height:48px;color:#fff;letter-spacing:-.3px}
.promo{position:absolute;left:866px;top:115px;width:186px;height:186px;border-radius:50%;background:rgba(32,42,94,.82);border:3px solid var(--gold);color:#fff;text-align:center}
.promo .star{position:absolute;left:70px;top:-2px;width:40px;height:40px;border-radius:50%;background:var(--gold)}
.promo .city{margin-top:50px;font-family:"Montserrat",Arial,sans-serif;font-size:22px;font-weight:600}
.promo .price{font-size:10px;margin-top:4px}
.promo .price b{font-size:17px;color:var(--gold-light)}
.promo .mini{position:absolute;left:0;bottom:0;width:180px;height:46px;border-radius:0 0 90px 90px;background:#e9e4d6;color:var(--navy);font-family:"Montserrat",Arial,sans-serif;font-weight:700;font-size:13px;line-height:30px}
.dots{position:absolute;right:4px;top:215px;display:flex;flex-direction:column;gap:9px}
.dots i{width:7px;height:7px;border-radius:50%;background:#fff;opacity:.8}

/* search panel */
.search{position:absolute;top:412px;left:0;width:1200px;height:206px;background:var(--navy)}
.search-tabs{position:absolute;top:29px;left:299px;display:flex;gap:5px}
.search-tabs span{display:block;height:32px;line-height:32px;padding:0 13px;font-size:12px;font-weight:600;color:#fff;background:var(--navy-deep)}
.search-tabs span.active{background:var(--gold)}
.fields{position:absolute;top:73px;left:141px;display:flex;gap:4px}
.field label{display:block;font-size:8px;font-weight:700;color:#fff;margin-bottom:4px;text-transform:uppercase}
.field .box{height:33px;background:#fff;display:flex;align-items:center;padding-left:9px;gap:7px;font-size:10px;color:#aaa}
.field .box.select{justify-content:space-between;padding:0 8px;color:#333;font-size:12px}
.addcar{position:absolute;top:153px;left:456px;font-size:12px;color:#fff;display:flex;align-items:center;gap:7px}
.addcar i{width:10px;height:10px;background:var(--gold-light)}
.btn{display:inline-block;background:var(--blue);color:#fff;font-weight:700;font-size:13px;text-align:center}
.search .btn{position:absolute;top:138px;left:553px;width:95px;height:41px;line-height:41px}

/* destinations */
.destinations{position:absolute;top:618px;left:0;width:1200px;height:645px}
.destinations h2{position:absolute;top:48px;width:1200px}
.destinations .tabs-inline{position:absolute;top:96px;width:1200px;color:var(--gold)}
.destinations .tabs-inline .on{color:var(--blue)}
.tile{position:absolute;overflow:hidden}
.tile::after{content:"";position:absolute;inset:8px;border:1px solid rgba(255,255,255,.55)}
.tile .name{position:absolute;left:20px;bottom:18px;color:#fff;font-weight:600;font-size:13px;z-index:1}
.t-ny{left:141px;top:160px;width:222px;height:407px;background:linear-gradient(180deg,#8fa2b3,#4a5f72 60%,#2c3a4c)}
.t-bkk{left:377px;top:160px;width:447px;height:193px;background:var(--blue-dark)}
.t-bkk .inner{position:absolute;inset:0;display:flex;flex-direction:column;align-items:center;justify-content:center;color:#fff;text-align:center;z-index:1}
.t-bkk h3{font-family:"Montserrat",Arial,sans-serif;font-weight:600;font-size:24px;margin-bottom:8px}
.t-bkk p{font-size:11px;line-height:15px}
.t-lv{left:377px;top:372px;width:447px;height:195px;background:linear-gradient(160deg,#5a4a7c,#b06a6a 45%,#e0954c 70%,#4b3a5c)}
.t-hi{left:838px;top:160px;width:221px;height:407px;background:linear-gradient(180deg,#cfd8da,#9aa58a 55%,#5e6a4a)}

/* hotels */
.hotels{position:absolute;top:1263px;left:0;width:1200px;height:477px;background:linear-gradient(180deg,#1d8ad2,#1774b8)}
.hotels h2{position:absolute;top:68px;width:1200px;color:#fff}
.hotels .tabs-inline{position:absolute;top:116px;width:1200px;color:#e6f1fa}
.hotels .tabs-inline .on{color:#fff}
.hotels .tabs-inline .sep{color:#9cc8ea}
.hotel{position:absolute;top:175px;width:292px;color:#fff}
.hotel .img{height:192px;border:2px solid rgba(255,255,255,.35)}
.hotel h4{font-size:12px;font-weight:700;margin-top:5px}
.hotel p{font-size:10px;color:#cfe4f3}
.hotel .stars{color:#f2c94c;font-size:10px;letter-spacing:1px;margin-top:4px}
.arrow{position:absolute;top:250px}

/* forum */
.forum{position:absolute;top:1740px;left:0;width:1200px;height:610px;background:var(--mist)}
.forum h2{position:absolute;top:52px;width:1200px}
.forum .sub{position:absolute;top:86px;width:1200px;text-align:center;color:var(--gold);font-size:11px;font-weight:600}
.table{position:absolute;top:132px;left:141px;width:918px;background:#fff;border:1px solid var(--line)}
.thead{height:38px;background:var(--gold);color:#fff;font-size:10px;font-weight:700;display:flex;align-items:center}
.row{height:66px;display:flex;align-items:center;border-top:1px solid var(--line)}
.c-title{width:548px;padding-left:23px}
.c-date{width:240px;font-size:10px;color:#555}
.c-stat{width:128px;text-align:right;padding-right:21px;font-size:9px;line-height:14px;color:#555}
.c-stat b{color:var(--gold);font-weight:400}
.row .c-title a{display:block;color:var(--gold);font-weight:600;font-size:13px;text-decoration:none}
.row .c-title small{font-size:9px;color:#555}
.row .c-date{align-self:flex-start;padding-top:14px}
.forum .btn{position:absolute;top:528px;left:553px;width:95px;height:32px;line-height:32px}

/* newsletter */
.newsletter{position:absolute;top:2350px;left:0;width:1200px;height:174px;background:linear-gradient(180deg,#1a73b6,#1e88cc 50%,#0f5a98)}
.newsletter h3{position:absolute;top:42px;width:1200px;text-align:center;font-family:"Montserrat",Arial,sans-serif;font-weight:700;font-size:18px;color:#fff}
.newsletter p{position:absolute;top:66px;width:1200px;text-align:center;font-size:11px;color:#e6f1fa}
.subscribe{position:absolute;top:94px;left:381px;display:flex}
.subscribe .input{width:348px;height:36px;background:#fff;display:flex;align-items:center;gap:9px;padding-left:13px;font-size:10px;color:#999}
.subscribe .go{width:88px;height:36px;line-height:36px;background:var(--gold);color:#fff;font-weight:700;font-size:14px;text-align:center}

/* popular links */
.links{position:absolute;top:2524px;left:0;width:1200px;height:430px}
.links h2{position:absolute;top:55px;width:1200px;font-size:25px}
.link-grid{position:absolute;top:117px;left:141px;display:grid;grid-template-columns:repeat(3,286px);column-gap:30px;row-gap:7px}
.link{position:relative;height:53px;display:flex;align-items:center;gap:14px;padding-left:15px;font-size:13px;font-weight:600;color:#444;border:1px solid #e6dcc4;border-right:none;width:272px;background:#fff}
.link::after{content:"";position:absolute;right:-14px;top:7px;width:37px;height:37px;border-top:1px solid #e6dcc4;border-right:1px solid #e6dcc4;transform:rotate(45deg) skew(10deg,10deg);background:#fff}

/* footer */
.footer{position:absolute;top:2951px;left:0;width:1200px;height:304px;background:linear-gradient(180deg,#ffffff 0%,#e6eef6 45%,#a9c3de 70%,#2c3f7a 86%,#1f2a5e 100%)}
.footer .fname{position:absolute;top:50px;width:1200px;text-align:center;font-family:"Montserrat",Arial,sans-serif;font-weight:700;font-size:30px;color:var(--navy)}
.footer nav{position:absolute;top:120px;width:1200px;display:flex;justify-content:center;gap:24px;font-size:10px;font-weight:700;color:#333}
.footer .copy{position:absolute;top:142px;width:1200px;text-align:center;font-size:10px;color:#555;letter-spacing:.3px}
</style>
</head>
<body>

<header class="topbar">
  <div class="utility"><span>ACCOUNT ▾</span><span>MY TRIPS</span><span>SUPPORT ▾</span></div>
  <nav class="nav left">
    <a class="active">HOME</a><a>HOLIDAYS</a><a>FLIGHTS</a><a>HOTELS</a>
  </nav>
  <nav class="nav right">
    <a>CARS</a><a>DEALS</a><a>INSURANCE</a><a>FORUM</a>
  </nav>
</header>
<svg class="logo-shield" viewBox="0 0 168 104" aria-hidden="true">
  <path d="M0 0 H168 V62 Q168 80 150 86 L84 104 L18 86 Q0 80 0 62 Z" fill="#fff"/>
</svg>
<div class="logo-text">rovanix</div>

<section class="hero" role="img" aria-label="Aerial photo of a turquoise bay with boats and a wooded coastline">
  <h1>START YOUR DREAM<br>HOLIDAYS RIGHT HERE</h1>
  <div class="promo">
    <div class="star"></div>
    <div class="city">Berlin</div>
    <div class="price">From <b>$500</b> per person</div>
    <div class="mini">rovanix</div>
  </div>
  <div class="dots"><i></i><i></i><i></i><i></i></div>
</section>

<section class="search">
  <div class="search-tabs">
    <span class="active">Flight &amp; Hotel</span><span>Holidays</span><span>Flights</span><span>Hotels</span><span>Cars</span><span>Insurance</span><span>Extras</span>
  </div>
  <div class="fields">
    <div class="field" style="width:228px"><label>Flying from</label><div class="box">
      <svg width="9" height="12" viewBox="0 0 9 12"><path d="M4.5 0A4.5 4.5 0 0 0 0 4.5C0 8 4.5 12 4.5 12S9 8 9 4.5A4.5 4.5 0 0 0 4.5 0Zm0 6.3a1.8 1.8 0 1 1 0-3.6 1.8 1.8 0 0 1 0 3.6Z" fill="#999"/></svg>City or Airport</div></div>
    <div class="field" style="width:228px"><label>Flying to</label><div class="box">
      <svg width="9" height="12" viewBox="0 0 9 12"><path d="M4.5 0A4.5 4.5 0 0 0 0 4.5C0 8 4.5 12 4.5 12S9 8 9 4.5A4.5 4.5 0 0 0 4.5 0Zm0 6.3a1.8 1.8 0 1 1 0-3.6 1.8 1.8 0 0 1 0 3.6Z" fill="#999"/></svg>City or Airport</div></div>
    <div class="field" style="width:121px"><label>Departing</label><div class="box">
      <svg width="11" height="11" viewBox="0 0 11 11"><rect x=".5" y="1.5" width="10" height="9" fill="none" stroke="#999"/><path d="M.5 4h10" stroke="#999"/></svg>dd/mm/yyyy</div></div>
    <div class="field" style="width:121px"><label>Returning</label><div class="box">
      <svg width="11" height="11" viewBox="0 0 11 11"><rect x=".5" y="1.5" width="10" height="9" fill="none" stroke="#999"/><path d="M.5 4h10" stroke="#999"/></svg>dd/mm/yyyy</div></div>
    <div class="field" style="width:52px"><label>Rooms</label><div class="box select">1<span>⌄</span></div></div>
    <div class="field" style="width:68px"><label>Adults (18+)</label><div class="box select">2<span>⌄</span></div></div>
    <div class="field" style="width:80px"><label>Children (0-17)</label><div class="box select">0<span>⌄</span></div></div>
  </div>
  <div class="addcar"><i></i>Add a Car</div>
  <span class="btn">Search</span>
</section>

<section class="destinations">
  <h2 class="section-title">DESTINATIONS</h2>
  <div class="tabs-inline"><span class="on">Top Destinations</span><span class="sep">|</span><span>Featured Destinations</span><span class="sep">|</span><span>Popular Destinations</span></div>
  <div class="tile t-ny" role="img" aria-label="New York skyscrapers seen from below"><span class="name">New York</span></div>
  <div class="tile t-bkk"><div class="inner"><h3>Bangkok</h3><p>Lorem ipsum dolor sit amet, consectetur adipiscing elit,<br>do eiusmod tempor incididunt ut labore.</p></div></div>
  <div class="tile t-lv" role="img" aria-label="Las Vegas welcome sign at sunset"><span class="name">Las Vegas</span></div>
  <div class="tile t-hi" role="img" aria-label="Hawaiian hula dancer holding flowers"><span class="name">Hawaii</span></div>
</section>

<section class="hotels">
  <h2 class="section-title">HOTELS</h2>
  <div class="tabs-inline"><span class="on">Luxury Hotels</span><span class="sep">|</span><span>Cheap Hotels</span><span class="sep">|</span><span>Popular Hotels</span></div>
  <svg class="arrow" style="left:85px" width="20" height="32" viewBox="0 0 20 32"><path d="M16 3 4 16l12 13" fill="none" stroke="#fff" stroke-width="3"/></svg>
  <svg class="arrow" style="left:1096px" width="20" height="32" viewBox="0 0 20 32"><path d="M4 3l12 13L4 29" fill="none" stroke="#fff" stroke-width="3"/></svg>
  <div class="hotel" style="left:141px">
    <div class="img" role="img" aria-label="Glass office towers in London" style="background:linear-gradient(160deg,#6fa6d6,#2d5f8e 50%,#8c6a4a)"></div>
    <h4>London, UK</h4><p>Fantacy Serviced Apartments</p><div class="stars">★★★★★</div>
  </div>
  <div class="hotel" style="left:454px">
    <div class="img" role="img" aria-label="Classic stone building facade in Paris" style="background:linear-gradient(170deg,#c8c5bd,#8d8a82 60%,#5f5c55)"></div>
    <h4>Paris, France</h4><p>Fantacy Serviced Apartments</p><div class="stars">★★★★★</div>
  </div>
  <div class="hotel" style="left:767px">
    <div class="img" role="img" aria-label="City towers lit at dusk" style="background:linear-gradient(180deg,#2a4f9a,#1c3570 55%,#c9873e)"></div>
    <h4>Paris, France</h4><p>Fantacy Serviced Apartments</p><div class="stars">★★★★★</div>
  </div>
</section>

<section class="forum">
  <h2 class="section-title">LATEST TRAVEL FORUM</h2>
  <div class="sub">Please share your experience here</div>
  <div class="table">
    <div class="thead"><span class="c-title">TITLE</span><span class="c-date">POSTED ON</span><span class="c-stat">VIEWS / REPLIES</span></div>
    <div class="row"><div class="c-title"><a>Why Hawaii is a hub for entertainment?</a><small>By : Tobin Marlowe</small></div><div class="c-date">15 Jan 2017, 07:45 AM</div><div class="c-stat">View : <b>1400</b><br>Replies : <b>45</b></div></div>
    <div class="row"><div class="c-title"><a>Whis the hottest place in January?</a><small>By : Ravel Osteni</small></div><div class="c-date">15 Jan 2017, 06:45 AM</div><div class="c-stat">View : <b>1950</b><br>Replies : <b>75</b></div></div>
    <div class="row"><div class="c-title"><a>Must visit destinations in the world which make you feel better...</a><small>By : Ravel Osteni</small></div><div class="c-date">15 Jan 2017, 06:45 AM</div><div class="c-stat">View : <b>1950</b><br>Replies : <b>75</b></div></div>
    <div class="row"><div class="c-title"><a>Why Hawaii is a hub for entertainment?</a><small>By : Tobin Marlowe</small></div><div class="c-date">15 Jan 2017, 07:45 AM</div><div class="c-stat">View : <b>1400</b><br>Replies : <b>45</b></div></div>
    <div class="row"><div class="c-title"><a>Whis the hottest place in January?</a><small>By : Ravel Osteni</small></div><div class="c-date">15 Jan 2017, 06:45 AM</div><div class="c-stat">View : <b>1950</b><br>Replies : <b>75</b></div></div>
  </div>
  <span class="btn">View All</span>
</section>

<section class="newsletter" role="img" aria-label="Blue sea with a moored boat and distant hills">
  <h3>SIGN UP TO OUR NEWSLETTER</h3>
  <p>Get updated for special offers</p>
  <div class="subscribe">
    <div class="input"><svg width="12" height="9" viewBox="0 0 12 9"><rect width="12" height="9" fill="#b99a55"/><path d="M0 0l6 5 6-5" fill="none" stroke="#fff"/></svg>Enter your email address</div>
    <div class="go">Submit</div>
  </div>
</section>

<section class="links">
  <h2 class="section-title">POPULAR LINKS YOU MAY INTERESTED</h2>
  <div class="link-grid">
    <a class="link"><svg width="13" height="10" viewBox="0 0 13 10"><path d="M1 5l4 4 7-8" fill="none" stroke="#b99a55" stroke-width="2"/></svg>New York Holidays</a>
    <a class="link"><svg width="13" height="10" viewBox="0 0 13 10"><path d="M1 5l4 4 7-8" fill="none" stroke="#b99a55" stroke-width="2"/></svg>Amsterdam Hotels</a>
    <a class="link"><svg width="13" height="10" viewBox="0 0 13 10"><path d="M1 5l4 4 7-8" fill="none" stroke="#b99a55" stroke-width="2"/></svg>Dubai Holidays</a>
    <a class="link"><svg width="13" height="10" viewBox="0 0 13 10"><path d="M1 5l4 4 7-8" fill="none" stroke="#b99a55" stroke-width="2"/></svg>UK Car Hire</a>
    <a class="link"><svg width="13" height="10" viewBox="0 0 13 10"><path d="M1 5l4 4 7-8" fill="none" stroke="#b99a55" stroke-width="2"/></svg>Oralando Flights</a>
    <a class="link"><svg width="13" height="10" viewBox="0 0 13 10"><path d="M1 5l4 4 7-8" fill="none" stroke="#b99a55" stroke-width="2"/></svg>Bangkok Flights</a>
    <a class="link"><svg width="13" height="10" viewBox="0 0 13 10"><path d="M1 5l4 4 7-8" fill="none" stroke="#b99a55" stroke-width="2"/></svg>Sydney Flights</a>
    <a class="link"><svg width="13" height="10" viewBox="0 0 13 10"><path d="M1 5l4 4 7-8" fill="none" stroke="#b99a55" stroke-width="2"/></svg>Hawaii Hotels</a>
    <a class="link"><svg width="13" height="10" viewBox="0 0 13 10"><path d="M1 5l4 4 7-8" fill="none" stroke="#b99a55" stroke-width="2"/></svg>Paris Car Hire</a>
    <a class="link"><svg width="13" height="10" viewBox="0 0 13 10"><path d="M1 5l4 4 7-8" fill="none" stroke="#b99a55" stroke-width="2"/></svg>New York Holidays</a>
    <a class="link"><svg width="13" height="10" viewBox="0 0 13 10"><path d="M1 5l4 4 7-8" fill="none" stroke="#b99a55" stroke-width="2"/></svg>Amsterdam Hotels</a>
    <a class="link"><svg width="13" height="10" viewBox="0 0 13 10"><path d="M1 5l4 4 7-8" fill="none" stroke="#b99a55" stroke-width="2"/></svg>Dubai Holidays</a>
    <a class="link"><svg width="13" height="10" viewBox="0 0 13 10"><path d="M1 5l4 4 7-8" fill="none" stroke="#b99a55" stroke-width="2"/></svg>UK Car Hire</a>
    <a class="link"><svg width="13" height="10" viewBox="0 0 13 10"><path d="M1 5l4 4 7-8" fill="none" stroke="#b99a55" stroke-width="2"/></svg>Oralando Flights</a>
    <a class="link"><svg width="13" height="10" viewBox="0 0 13 10"><path d="M1 5l4 4 7-8" fill="none" stroke="#b99a55" stroke-width="2"/></svg>Bangkok Flights</a>
  </div>
</section>

<footer class="footer" role="img" aria-label="City skyline silhouette in navy under a pale sky">
  <div class="fname">rovanix</div>
  <nav><span>HOME</span><span>ABOUT US</span><span>CUSTOMER SUPPORT</span><span>PRIVACY</span><span>TERMS OF USE</span></nav>
  <div class="copy">© 2016 ROVANIX. ALL RIGHTS RESERVED.</div>
</footer>

</body>
</html>
```